Modern & Simple Essential Oils Label

Company Name: Meadowlark Essentials

What we sell: Aromatherapy products, pure therapeutic essential oils.

Design need:
We are looking for a creative and youthful design for the labels used on small essentials oils.

I have two sizes of bottles that I use for essential oils a 5ml bottle and a 15ml bottle. They are dark Amber color glass with black lids. I like the clear labels or mayble a dark brown background. With white or clear lettering with punch of color too! Each oil type is represented by different color. (lavender- purple, lemon - yellow). The label will be the same for all the oils in the two sizes with only a different oil name & coordinating color.
5ml label size should be: 1 " x 2.625"
15ml label size should be: 1.5" x 3.5"

I have some labels that I have had another designer start on, but they aren't quite what I want and missing that something (alot!).. I don't know what. Interest maybe? Lack of design? I dunno.. they are attached. Maybe it's the logo? I don't know! But its gotta change! When I cut out a proof and put a sample on the bottle as I look straight on at the label all I see is a big dot, no logo.. nothing interesting.
Updates

Project Deadline Extended
Reason: Hi! Id like to extend this deadline. Ive been unavailable for a few days due to an illness and Im so far behind! Im feeling MUCH better and looking forward to getting caught up and move with the project. Im not sure how this works, but I attached a list of the oils that we currently have available. And in the list is the idea for the color schemes for the oils. The basic idea is for it to have a wide array of colors, so using different shades of greens, yellows, oranges and so on. So that its like a rainbow. We are not set of that particular color for that particular oil. It was just a idea list of possible colors for oils. Thanks so much!

Target Market(s)

Metro & Modern people. Interested in healthy organic living, Mostly women (some men) 20-45 who are interested in holistic healing.

Industry/Entity Type

It Company

Requirements
Must have
• A reputable look. Clean, organic, crisp, zen or spa-like feel. Modern, youthful appealing label design. Approachable and interesting, not intimidating so that I don't turn away people who are new or not familiar with how to use essential oils.
Should not have
• do NOT want the look to be anywhere close to medicinal, witchy, crafty, hippie, mystical, overly earthy, magical, or voodoo. Do not want it to look like something out of a grandmothers medicine cabinet.

```html
<!DOCTYPE html>
<html lang="en">
<head>
<meta charset="utf-8">
<title>Meadowlark Essentials – Essential Oil Labels</title>
<link rel="stylesheet" href="https://fonts.googleapis.com/css2?family=Roboto+Slab:wght@300;400;500;600&display=swap">
<style>
  :root {
    --paper: #ffffff;
    --bark: #532a14;
    --lemon: #d6e022;
    --lavender: #ae8dc5;
  }
  html, body {
    margin: 0;
    padding: 0;
    overflow: hidden;
  }
  body {
    width: 1200px;
    height: 848px;
    background: var(--paper);
    position: relative;
    font-family: "Roboto Slab", Georgia, serif;
  }
  .label {
    position: absolute;
    display: flex;
    flex-direction: column;
    background: var(--bark);
    overflow: hidden;
  }
  .label--lemon { --accent: var(--lemon); }
  .label--lavender { --accent: var(--lavender); }

  .label__band {
    background: var(--accent);
    color: var(--bark);
    display: flex;
    align-items: center;
    justify-content: center;
    white-space: nowrap;
    font-weight: 500;
    line-height: 1;
  }
  .label__body {
    flex: 1;
    display: flex;
    flex-direction: column;
    align-items: center;
    justify-content: center;
    color: var(--accent);
  }
  .brand-dot {
    background: var(--accent);
    border-radius: 50%;
    flex: none;
  }
  .oil-name {
    margin: 0;
    text-align: center;
    line-height: 1;
  }
  .oil-name__lead { display: block; font-weight: 300; }
  .oil-name__main { display: block; font-weight: 600; }

  /* 5 ml, stacked layout */
  .label--small { width: 270px; height: 102px; }
  .label--small .label__band { height: 14px; font-size: 9.5px; }
  .label--small .brand-dot { width: 24px; height: 24px; margin-bottom: 7px; }
  .label--small .oil-name__lead { font-size: 12px; }
  .label--small .oil-name__main { font-size: 12px; margin-top: 1px; }

  /* 15 ml, stacked layout */
  .label--large { width: 359px; height: 154px; }
  .label--large .label__band { height: 19px; font-size: 13px; }
  .label--large .label__band--foot { height: 16px; font-size: 12px; font-weight: 400; }
  .label--large .brand-dot { width: 40px; height: 40px; margin-bottom: 14px; }
  .label--large .oil-name__lead { font-size: 18px; }
  .label--large .oil-name__main { font-size: 18px; margin-top: 2px; }

  /* 5 ml, horizontal brand layout */
  .label--wide { width: 269px; height: 102px; }
  .label--wide .label__band { height: 15px; font-size: 9px; }
  .label--wide .label__body { flex-direction: row; gap: 7px; }
  .label--wide .brand-dot { width: 34px; height: 34px; }
  .brand-name {
    font-weight: 400;
    font-size: 20px;
    color: var(--accent);
    white-space: nowrap;
  }
</style>
</head>
<body>

  <!-- 5 ml stacked -->
  <article class="label label--small label--lemon" style="left:83px; top:308px;">
    <div class="label__band">meadowlark essentials</div>
    <div class="label__body">
      <span class="brand-dot"></span>
      <p class="oil-name"><span class="oil-name__lead">sunny</span><span class="oil-name__main">lemon</span></p>
    </div>
    <div class="label__band">PURE ESSENTIAL OIL</div>
  </article>

  <article class="label label--small label--lavender" style="left:82px; top:438px;">
    <div class="label__band">meadowlark essentials</div>
    <div class="label__body">
      <span class="brand-dot"></span>
      <p class="oil-name"><span class="oil-name__lead">softly sweet</span><span class="oil-name__main">lavender</span></p>
    </div>
    <div class="label__band">PURE ESSENTIAL OIL</div>
  </article>

  <!-- 15 ml stacked -->
  <article class="label label--large label--lemon" style="left:421px; top:259px;">
    <div class="label__band">meadowlark essentials</div>
    <div class="label__body">
      <span class="brand-dot"></span>
      <p class="oil-name"><span class="oil-name__lead">sunny</span><span class="oil-name__main">lemon</span></p>
    </div>
    <div class="label__band label__band--foot">PURE ESSENTIAL OIL</div>
  </article>

  <article class="label label--large label--lavender" style="left:421px; top:435px;">
    <div class="label__band">meadowlark essentials</div>
    <div class="label__body">
      <span class="brand-dot"></span>
      <p class="oil-name"><span class="oil-name__lead">softly sweet</span><span class="oil-name__main">lavender</span></p>
    </div>
    <div class="label__band label__band--foot" style="height:19px;">PURE ESSENTIAL OIL</div>
  </article>

  <!-- 5 ml horizontal brand -->
  <article class="label label--wide label--lemon" style="left:849px; top:308px;">
    <div class="label__band">SUNNY LEMON • PURE ESSENTIAL OIL • SUNNY LEMON</div>
    <div class="label__body">
      <span class="brand-dot"></span>
      <span class="brand-name">meadowlark essentials</span>
    </div>
    <div class="label__band">SUNNY LEMON • PURE ESSENTIAL OIL • SUNNY LEMON</div>
  </article>

  <article class="label label--wide label--lavender" style="left:849px; top:438px;">
    <div class="label__band">SOFTLY SWEET LAVENDER • PURE ESSENTIAL OIL</div>
    <div class="label__body">
      <span class="brand-dot"></span>
      <span class="brand-name">meadowlark essentials</span>
    </div>
    <div class="label__band">SOFTLY SWEET LAVENDER • PURE ESSENTIAL OIL</div>
  </article>

</body>
</html>
```